Marwick Family Chiropractic Stationary

The letterhead and business card must have our logo.
We would like to see the logo used in different ways ( It can be expanded upon in the stationary.)
Please use the the same or similar colors.
Must be eye catching and memorable.
Must be easy to read

Reason: The doctor has been too busy to make any final decisions. He would like to give himself a little more time.

Target Market(s)

Chiropractic Healthcare

Industry/Entity Type

Business

Requirements
Must have
• Dr. Leonard Marwick D.C.
Chiropractor

860-555-0183

417 Birchfield Road, 2nd Floor
Vernon, CT 06091

drmarwick@marwickspine.example
www.marwickspine.example
www.facebook.com/MarwickFamilySpine
Should not have
• should not be difficult to read

```html
<!DOCTYPE html>
<html lang="en">
<head>
<meta charset="UTF-8">
<title>Marwick Family Chiropractic – CD Variant 1</title>
<link href="https://fonts.googleapis.com/css2?family=Montserrat:wght@700&family=Open+Sans:ital,wght@0,400;0,600;1,400;1,700&display=swap" rel="stylesheet">
<style>
  :root {
    --bg: #eeeeec;
    --paper: #ffffff;
    --green: #2f9a12;
    --green-dark: #247c0c;
    --leaf-lime: #b4e020;
    --leaf-yellow: #f0e020;
    --leaf-olive: #b3a020;
    --trunk: #3a2a20;
    --ink: #333333;
    --label: #b4b4b4;
    --hub: #d6d6d6;
    --hub-inner: #e6e6e6;
    --social: #3b74c9;
  }
  * { margin: 0; padding: 0; box-sizing: border-box; }
  html, body { width: 1200px; height: 868px; overflow: hidden; }
  body {
    background: var(--bg);
    font-family: "Open Sans", Arial, sans-serif;
    position: relative;
  }
  .presentation-label {
    position: absolute; left: 55px; top: 44px;
    color: var(--label); font-size: 17px; line-height: 23px;
  }
  .presentation-label .type { font-weight: 700; margin-bottom: 24px; }
  .presentation-label .client { font-style: italic; margin-bottom: 22px; }
  .presentation-label .variant { font-style: italic; font-weight: 700; }

  .sleeve {
    position: absolute; left: 170px; top: 210px;
    width: 440px; height: 440px;
    background: var(--paper);
    box-shadow: 0 6px 18px rgba(0,0,0,.12);
    overflow: hidden;
  }
  .brand-mark {
    position: absolute; left: 140px; top: 56px;
    display: flex; align-items: center; gap: 8px;
    color: var(--green);
    font-family: "Montserrat", Arial, sans-serif; font-weight: 700;
    font-size: 15px; line-height: 1.15; text-transform: uppercase;
  }
  .brand-mark .dot { width: 40px; height: 40px; border-radius: 50%; background: var(--green); flex: none; }
  .sleeve .tree-art {
    position: absolute; right: 20px; bottom: 100px;
    width: 160px; height: 200px;
    background: linear-gradient(170deg, var(--leaf-yellow), var(--leaf-lime) 45%, var(--green) 72%, var(--trunk));
    border-radius: 50% 50% 12% 40%;
  }
  .contact-row {
    position: absolute; left: 28px; bottom: 62px;
    display: flex; gap: 28px; font-size: 10px; line-height: 16px; color: var(--ink);
    white-space: nowrap;
  }
  .contact-item { display: flex; align-items: center; gap: 6px; }
  .contact-item svg { width: 14px; height: 14px; flex: none; }
  .sleeve .band { position: absolute; left: 0; bottom: 0; width: 440px; height: 60px; }

  .disc { position: absolute; left: 690px; top: 250px; }
</style>
</head>
<body>
  <div class="presentation-label">
    <p class="type">CD</p>
    <p class="client">Marwick Family<br>Chiropractic</p>
    <p class="variant">Variant 1</p>
  </div>

  <section class="sleeve">
    <div class="brand-mark"><span class="dot"></span><span>Marwick<br>Family Chiropractic</span></div>
    <div class="tree-art" role="img" aria-label="Tree of coloured leaves rising from a figure-shaped trunk"></div>
    <div class="contact-row">
      <span class="contact-item">
        <svg viewBox="0 0 16 16"><circle cx="8" cy="8" r="8" fill="var(--green)"/><circle cx="8" cy="8" r="5" fill="none" stroke="#fff" stroke-width="1"/><path d="M3 8h10M8 3v10" stroke="#fff" stroke-width="1"/></svg>
        www.marwickspine.example
      </span>
      <span class="contact-item">
        <svg viewBox="0 0 16 16"><circle cx="8" cy="8" r="8" fill="var(--social)"/></svg>
        /MarwickFamilySpine
      </span>
    </div>
    <svg class="band" viewBox="0 0 440 60" preserveAspectRatio="none">
      <path d="M0 20 L440 52 L440 60 L0 60 Z" fill="var(--green)"/>
      <path d="M300 60 Q360 30 440 40 L440 60 Z" fill="var(--green-dark)"/>
    </svg>
  </section>

  <svg class="disc" width="420" height="420" viewBox="0 0 420 420">
    <defs>
      <clipPath id="disc-clip"><circle cx="210" cy="210" r="205"/></clipPath>
      <linearGradient id="tree-tones" x1="0" y1="0" x2="0.3" y2="1">
        <stop offset="0" stop-color="#f0e020"/><stop offset=".45" stop-color="#b4e020"/>
        <stop offset=".7" stop-color="#2f9a12"/><stop offset="1" stop-color="#3a2a20"/>
      </linearGradient>
    </defs>
    <circle cx="210" cy="214" r="205" fill="rgba(0,0,0,.1)"/>
    <circle cx="210" cy="210" r="205" fill="var(--paper)"/>
    <g clip-path="url(#disc-clip)">
      <path d="M0 250 Q120 430 420 330 L420 420 L0 420 Z" fill="var(--green)"/>
    </g>
    <circle cx="210" cy="210" r="62" fill="var(--hub)"/>
    <circle cx="210" cy="210" r="40" fill="var(--hub-inner)"/>
    <circle cx="210" cy="210" r="18" fill="var(--bg)"/>
    <g font-family="Montserrat, Arial, sans-serif" font-weight="700" fill="var(--green)">
      <circle cx="88" cy="108" r="16" fill="var(--green)"/>
      <text x="110" y="104" font-size="13">MARWICK</text>
      <text x="110" y="120" font-size="9">FAMILY CHIROPRACTIC</text>
    </g>
    <rect x="280" y="150" width="110" height="190" rx="50" fill="url(#tree-tones)" role="img" aria-label="Tree of coloured leaves rising from a figure-shaped trunk"/>
  </svg>
</body>
</html>
```